Web Calculator design Housing Investment

We have a web calculator that needs to be fixed from a design perspective. The key tasks are:<br/>1. Selecting icons / pictures / colours for the various steps<br/>2. Designing navigation between calculator steps<br/>3. Making suggestions for chart design. The limitation is that the charts are all using the Vextra API (the same charts that Vextra Grids use).<br/><br/>There are four entry screens and then a result screen. See attached PDF for screenshots. You can see our website at https://larkhollowfunds.com for our corporate colours and style.

Target Market(s)

Real Estate Investors

Industry/Entity Type

Financial Planning

Number of Pages Required

1 page

Font styles to use
Sans Serif
Other font styles liked:
• Ubuntu

Colors
86cae7
3176b5
0455a3
ffffff

Requirements
Must have
• New Icons
• Suggested design for navigation
• Suggested design for charts

```html
<!DOCTYPE html>
<html lang="en">
<head>
<meta charset="utf-8">
<title>Housing Investment Calculator</title>
<link rel="stylesheet" href="https://fonts.googleapis.com/css2?family=Poppins:ital,wght@0,300;0,400;0,500;0,600;1,500&family=Roboto+Condensed:wght@400&display=swap">
<style>
:root{
  --navy:#0455a3;
  --blue:#3176b5;
  --sky:#86cae7;
  --white:#ffffff;
  --ink:#2b2b2b;
  --muted:#5f6b78;
  --faint:#7ea6d3;
  --pale:#c3d6ec;
  --track:#d9d9d9;
  --line:#e6e9ee;
  --red:#e02b2b;
  --wood-dark:#4a2410;
  --wood-mid:#7a3f1c;
  --wood-light:#b9783e;
}
*{box-sizing:border-box;margin:0;padding:0}
html,body{width:1200px;height:3443px;overflow:hidden}
body{
  position:relative;
  font-family:"Poppins",sans-serif;
  color:var(--ink);
  background:linear-gradient(90deg,var(--wood-dark) 0%,var(--wood-mid) 30%,var(--wood-light) 50%,var(--wood-mid) 70%,var(--wood-dark) 100%);
}
.backdrop{position:absolute;inset:0}
.screen{position:absolute;background:var(--white)}
.screen--1{left:80px;top:60px;width:1040px;height:561px}
.screen--2{left:76px;top:770px;width:1049px;height:641px}
.screen--3{left:80px;top:1583px;width:1040px;height:667px}
.screen--4{left:80px;top:2461px;width:1040px;height:806px}
.screen-label{
  position:absolute;left:0;width:1200px;text-align:center;
  color:var(--white);font-weight:300;font-size:38px;letter-spacing:1px;line-height:1;
}
.title{
  position:absolute;left:0;right:0;text-align:center;
  font-style:italic;font-weight:500;font-size:31px;color:#111;line-height:1;
}
.title b{color:var(--navy);font-weight:500}
.steps{position:absolute;left:50%;width:785px;margin-left:-392px;display:flex;justify-content:space-between}
.step{
  width:128px;height:100px;background:var(--white);
  box-shadow:0 3px 4px rgba(0,0,0,.18),0 0 0 1px #eceff3;
  display:flex;flex-direction:column;align-items:center;justify-content:center;gap:8px;
  font-family:"Roboto Condensed",sans-serif;font-size:14px;color:var(--faint);
}
.step svg{width:46px;height:44px;stroke:var(--pale);fill:none;stroke-width:1.6}
.step--on{color:var(--navy)}
.step--on svg{stroke:var(--navy)}
.progress{position:absolute;left:50%;width:785px;margin-left:-392px;height:10px;border-radius:5px;background:var(--track);overflow:hidden}
.progress span{
  display:block;height:100%;border-radius:5px;
  background:repeating-linear-gradient(115deg,var(--navy) 0 4px,var(--blue) 4px 7px);
}
.question{position:absolute;left:0;right:0;text-align:center;font-size:15px;font-weight:500;color:#333}
.pager{
  position:absolute;left:0;right:0;display:flex;justify-content:center;align-items:center;gap:7px;
  font-size:11px;font-weight:600;color:#444;
}
.pager i{display:flex;gap:2px}
.pager i em{width:16px;height:13px;border:1px solid #888;font-style:normal;font-size:9px;line-height:11px;text-align:center;color:#777}
.choice{
  position:absolute;background:var(--white);box-shadow:0 2px 6px rgba(0,0,0,.16);
  display:flex;flex-direction:column;align-items:center;
}
.radio{display:flex;align-items:center;gap:10px;font-size:15px;color:#333;position:absolute;bottom:14px}
.radio::before{content:"";width:13px;height:13px;border-radius:50%;background:#d4d4d4}
.radio--on{color:var(--navy)}
.radio--on::before{background:var(--navy);box-shadow:0 0 0 2px #cfe0f2}
.choice svg{margin-top:14px}
.map{position:absolute;left:102px;top:329px;width:224px;height:200px;background:linear-gradient(135deg,var(--pale),#7ea6d3);border-radius:40% 45% 35% 45%}
.field-label{position:absolute;font-size:14px;font-weight:500;color:#333}
.slider{position:absolute;left:386px;width:293px;height:8px;border-radius:4px;background:#e0e0e0}
.slider span{position:absolute;top:-5px;width:18px;height:18px;border-radius:50%;background:var(--navy)}
.amount{position:absolute;left:780px;font-size:15px;font-weight:500;color:var(--navy)}
.method-note{position:absolute;width:200px;font-size:14px;line-height:20px;color:#333}
.forecast-text{position:absolute;left:215px;font-size:14px;line-height:20px;color:#333;width:400px}
.select{
  position:absolute;left:639px;width:176px;height:32px;background:var(--white);
  box-shadow:0 1px 4px rgba(0,0,0,.2);padding:0 10px;
  display:flex;align-items:center;justify-content:space-between;
  font-family:"Roboto Condensed",sans-serif;font-size:14px;color:var(--navy);
}
.select::after{content:"v";font-size:9px;color:#666}
.legend{position:absolute;left:0;right:0;top:441px;display:flex;justify-content:center;gap:12px;font-size:11px;color:#555}
.legend span{display:flex;align-items:center;gap:5px}
.legend span::before{content:"";width:24px;height:2px;background:var(--navy)}
.legend .legend-red::before{background:var(--red)}
.chart{position:absolute;left:0;top:470px;width:1040px;height:150px}
.chart text{font-family:"Poppins",sans-serif;font-size:11px;fill:#555}
.note{position:absolute;left:0;right:0;top:650px;text-align:center;font-size:11px;line-height:17px;color:#555}
</style>
</head>
<body>
<div class="backdrop"></div>

<svg width="0" height="0" style="position:absolute">
  <defs>
    <symbol id="ic-type" viewBox="0 0 46 44"><path d="M3 40h40M6 40V24l10-7 10 7v16M26 40V14l7-6 7 6v26M10 27h4v4h-4zM17 27h4v4h-4zM10 33h11M30 18h6M30 24h6M30 30h6"/></symbol>
    <symbol id="ic-pin" viewBox="0 0 46 44"><path d="M23 4a10 10 0 0 1 10 10c0 8-10 18-10 18S13 22 13 14A10 10 0 0 1 23 4z"/><circle cx="23" cy="14" r="4"/><ellipse cx="23" cy="36" rx="13" ry="4"/></symbol>
    <symbol id="ic-value" viewBox="0 0 46 44"><path d="M9 4h20l6 6v16M9 4v34h16M15 18l6-5 6 5v7H15z"/><circle cx="31" cy="32" r="6"/><path d="M35 36l5 5"/></symbol>
    <symbol id="ic-forecast" viewBox="0 0 46 44"><path d="M6 40h34M8 22l15-14 15 14M12 20v10M34 20v10M23 13v12M20 16h5a2 2 0 0 1 0 4h-4a2 2 0 0 0 0 4h5M12 34l8-5 6 3 10-8M8 40v-3M14 40v-4M32 40v-3M38 40v-5"/></symbol>
    <symbol id="ic-calc" viewBox="0 0 46 44"><path d="M4 24l12-10 12 10M8 22v18h16V28M12 34h6M22 4h18v22H28M25 8h12v5H25zM25 17h3M30 17h3M35 17h2M30 21h3M35 21h2"/></symbol>
  </defs>
</svg>

<!-- Screen 1 -->
<section class="screen screen--1">
  <h1 class="title" style="top:49px"><b>H</b>ousing <b>I</b>nvestment <b>C</b>alculator</h1>
  <nav class="steps" style="top:114px">
    <div class="step step--on"><svg><use href="#ic-type"/></svg>Property Type</div>
    <div class="step"><svg><use href="#ic-pin"/></svg>Property Location</div>
    <div class="step"><svg><use href="#ic-value"/></svg>Property Valuation</div>
    <div class="step"><svg><use href="#ic-forecast"/></svg>Property Forecast</div>
    <div class="step"><svg><use href="#ic-calc"/></svg>Calculator</div>
  </nav>
  <div class="progress" style="top:234px"><span style="width:15%"></span></div>
  <p class="question" style="top:268px">What type of property would you like to compare ?</p>
  <div class="choice" style="left:337px;top:305px;width:172px;height:148px">
    <svg width="92" height="86" viewBox="0 0 92 86" fill="none" stroke="var(--navy)" stroke-width="2.4"><path d="M4 84h84M8 84V20h28v64M36 84V6h44v78M14 28h7v7h-7zM25 28h7v7h-7zM14 42h7v7h-7zM25 42h7v7h-7zM14 56h7v7h-7zM25 56h7v7h-7zM44 14h10v10H44zM62 14h10v10H62zM44 32h10v10H44zM62 32h10v10H62zM52 84V58h14v26"/></svg>
    <span class="radio radio--on">Unit</span>
  </div>
  <div class="choice" style="left:529px;top:305px;width:172px;height:148px">
    <svg width="92" height="86" viewBox="0 0 92 86" fill="none" stroke="var(--pale)" stroke-width="2.4"><path d="M4 84h84M46 6L8 30h76zM12 30v54M80 30v54M38 20h16M22 40h10v10H22zM60 40h10v10H60zM22 60h10v10H22zM60 60h10v10H60zM40 84V56h12v28M42 36h8v10h-8z"/></svg>
    <span class="radio">Property</span>
  </div>
  <div class="pager" style="top:485px">Previous<i><em>&lt;</em><em>&gt;</em></i>Next</div>
</section>
<p class="screen-label" style="top:652px">Screen 1</p>

<!-- Screen 2 -->
<section class="screen screen--2">
  <h1 class="title" style="top:52px"><b>H</b>ousing <b>I</b>nvestment <b>C</b>alculator</h1>
  <nav class="steps" style="top:114px">
    <div class="step step--on"><svg><use href="#ic-type"/></svg>Property Type</div>
    <div class="step step--on"><svg><use href="#ic-pin"/></svg>Property Location</div>
    <div class="step"><svg><use href="#ic-value"/></svg>Property Valuation</div>
    <div class="step"><svg><use href="#ic-forecast"/></svg>Property Forecast</div>
    <div class="step"><svg><use href="#ic-calc"/></svg>Calculator</div>
  </nav>
  <div class="progress" style="top:232px"><span style="width:40%"></span></div>
  <p class="question" style="top:283px">Where would these property would be located ?</p>
  <div class="map" role="img" aria-label="Map of Australia with selectable states shaded in blue tones"></div>
  <span class="field-label" style="left:461px;top:367px">How much will the property cost?</span>
  <div class="slider" style="top:403px"><span style="left:47px"></span></div>
  <span class="amount" style="top:396px">$ 500,000</span>
  <span class="field-label" style="left:463px;top:440px">How much will you invest?</span>
  <div class="slider" style="top:477px;left:388px"><span style="left:20px"></span></div>
  <span class="amount" style="top:469px">$ 200,000</span>
  <div class="pager" style="top:560px">Previous<i><em>&lt;</em><em>&gt;</em></i>Next</div>
</section>
<p class="screen-label" style="top:1448px">Screen 2</p>

<!-- Screen 3 -->
<section class="screen screen--3">
  <h1 class="title" style="top:56px"><b>H</b>ousing <b>I</b>nvestment <b>C</b>alculator</h1>
  <nav class="steps" style="top:116px">
    <div class="step step--on"><svg><use href="#ic-type"/></svg>Property Type</div>
    <div class="step step--on"><svg><use href="#ic-pin"/></svg>Property Location</div>
    <div class="step step--on"><svg><use href="#ic-value"/></svg>Property Valuation</div>
    <div class="step"><svg><use href="#ic-forecast"/></svg>Property Forecast</div>
    <div class="step"><svg><use href="#ic-calc"/></svg>Calculator</div>
  </nav>
  <div class="progress" style="top:234px"><span style="width:60%"></span></div>
  <p class="question" style="top:284px">How would you like to forecast the returns from property ?</p>
  <div class="choice" style="left:168px;top:333px;width:192px;height:148px">
    <svg width="100" height="76" viewBox="0 0 100 76" fill="var(--navy)" stroke="var(--navy)" stroke-width="2.4"><path d="M50 6v60M30 72h40v-6H30zM14 16h72" fill="none"/><circle cx="50" cy="8" r="4"/><path d="M14 16L4 40M14 16l10 24M86 16L76 40M86 16l10 24" fill="none"/><path d="M2 40h24a12 8 0 0 1-24 0zM74 40h24a12 8 0 0 1-24 0z"/></svg>
    <span class="radio radio--on">Relative Cost</span>
  </div>
  <div class="choice" style="left:422px;top:333px;width:192px;height:148px">
    <div role="img" aria-label="Icon of an office worker beside a stack of banknotes" style="margin-top:16px;width:84px;height:76px;background:linear-gradient(180deg,#e4e7ec,#c9ced6);border-radius:6px"></div>
    <span class="radio">Relative to wages</span>
  </div>
  <div class="choice" style="left:676px;top:333px;width:192px;height:148px">
    <svg width="84" height="76" viewBox="0 0 84 76" fill="none" stroke="#9aa3ad" stroke-width="2"><circle cx="30" cy="30" r="22"/><path d="M36 20h-9a5 5 0 0 0 0 10h6a5 5 0 0 1 0 10h-10M30 14v4M30 42v4M24 66l16-14 8 6 20-20M62 38h6v6M66 6v10M61 11h10M76 24v6M73 27h6M8 56v6M5 59h6"/></svg>
    <span class="radio">Using Rental Yiled</span>
  </div>
  <p class="method-note" style="left:171px;top:498px">Use this to value property based on mortage cost relative to rent cost</p>
  <p class="method-note" style="left:428px;top:498px">Use this to value property based on mortage cost relative to wages</p>
  <p class="method-note" style="left:679px;top:498px">Use this to value property based on a rental yield</p>
  <div class="pager" style="top:594px">Previous<i><em>&lt;</em><em>&gt;</em></i>Next</div>
</section>
<p class="screen-label" style="top:2303px">Screen 3</p>

<!-- Screen 4 -->
<section class="screen screen--4">
  <h1 class="title" style="top:54px"><b>H</b>ousing <b>I</b>nvestment <b>C</b>alculator</h1>
  <nav class="steps" style="top:114px">
    <div class="step step--on"><svg><use href="#ic-type"/></svg>Property Type</div>
    <div class="step step--on"><svg><use href="#ic-pin"/></svg>Property Location</div>
    <div class="step step--on"><svg><use href="#ic-value"/></svg>Property Valuation</div>
    <div class="step step--on"><svg><use href="#ic-forecast"/></svg>Property Forecast</div>
    <div class="step"><svg><use href="#ic-calc"/></svg>Calculator</div>
  </nav>
  <div class="progress" style="top:232px"><span style="width:80%"></span></div>
  <p class="question" style="top:280px">Your Property Price Forecast</p>
  <p class="forecast-text" style="top:319px">You have chosen to forecast property price using</p>
  <div class="select" style="top:314px">Gross Rental Yield</div>
  <p class="forecast-text" style="top:358px">You can see how this ratio has changed over time (in blue) below vs your assumption (in red) for</p>
  <div class="select" style="top:362px">Sydney House</div>
  <div class="legend"><span>Gross Rental Yield</span><span class="legend-red">Forecast</span></div>
  <svg class="chart" viewBox="0 470 1040 150">
    <g stroke="var(--line)" stroke-width="1">
      <path d="M307 488H770M307 522.7H770M307 557.4H770M307 592H770"/>
      <path d="M357 488V592M403.4 488V592M449.8 488V592M496 488V592M542.5 488V592M589 488V592M635.2 488V592M681.6 488V592M728 488V592M770 488V592"/>
    </g>
    <text x="279" y="492">15%</text><text x="279" y="527">10%</text><text x="283" y="561">5%</text><text x="283" y="596">0%</text>
    <g text-anchor="middle">
      <text x="357" y="612">1985</text><text x="403" y="612">1990</text><text x="450" y="612">1995</text><text x="496" y="612">2000</text><text x="542" y="612">2005</text><text x="589" y="612">2010</text><text x="635" y="612">2015</text><text x="682" y="612">2020</text><text x="728" y="612">2025</text>
    </g>
    <polyline fill="none" stroke="var(--navy)" stroke-width="1.6" points="313,530 320,540 329,533 338,547 348,537 357,534 366,530 375,528 385,523 394,530 403,537 413,530 422,533 431,533 441,537 450,540 459,541 468,544 478,545 487,547 496,550 505,554 515,558 524,564 533,566 542,568 552,565 561,561 570,563 580,564 589,561 598,557 607,560 617,561 626,563 635,564 645,566 654,568 663,567 672,567 682,568"/>
    <line x1="672" y1="568.4" x2="770" y2="568.4" stroke="var(--red)" stroke-width="1.6"/>
  </svg>
  <p class="note">By default we assume the ratio stays at the lates value of 3.4%<br>You can change this assumption using the slider</p>
  <div class="pager" style="top:735px">Previous<i><em>&lt;</em><em>&gt;</em></i>Next</div>
</section>
<p class="screen-label" style="top:3309px">Screen 4</p>
</body>
</html>
```